skyPARLOR Helicopter Tour WordPress Website Design

SkyPARLOR (skyparlor-example.com) is a premium helicopter tour company offering scenic flights in two Florida cities: Tampa and Sarasota. We are seeking a full Wordpress website redesign that is modern, upbeat, inviting, and highly conversion‑focused. The new site should feel energetic and trustworthy, reflect the excitement of helicopter sightseeing, and maintain our recognizable SkyPARLOR color palette—while updating the overall look to feel fresh, clean, and current.
The website must be SEO‑friendly, mobile‑optimized, and easy to navigate. It should highlight our 5‑star customer reviews, showcase our tours clearly, and integrate seamlessly with TrailDock for instant online booking. The design should support a premium aviation experience while remaining friendly and accessible to tourists, families, couples, and adventure seekers.

These elements are essential and must be included in the design:

Brand & UX:
- Modern, upbeat, inviting design
- SEO‑friendly structure and layout
- Easy navigation and clear user flow
- Light grey “SP” background logo watermark (as used on current site)
- Clean, aviation‑inspired typography and layout

Conversion Features:
- Instant booking above the fold (TrailDock integration)
- Live Orbin Ratings carousel
- Tour comparison table (duration, route, price, etc.)
- FAQ expandable section
- Gift Cards page (highlighted as a major offering)
- What to Expect timeline (Arrive → Check‑In → Safety Briefing → Flight → Photos)
- Weather transparency widget (clear messaging about weather‑dependent flights

Content Structure:
- Separate pages for Tampa, Sarasota, and Gender Reveal Flights
- Pilot/Team profiles with short bios
- Highlighted features:
- Doors‑Off option
- Sunset flights
- Romantic packages
- Champagne add‑ons

Colors:
Use the existing SkyPARLOR palette as the foundation, but modernize it.
- Background: Clean with the light grey “SP” watermark integrated tastefully.
The overall color direction should feel bright, premium, energetic, and trustworthy

Target Market(s)

Tourists visiting Tampa or Sarasota, Families looking for memorable activities, Couples seeking romantic experiences (sunset flights, proposals, anniversaries), Adventure seekers and content creators, Locals celebrating birthdays, holidays, or special occasions, Gender reveal clients looking for a unique aerial reveal experience

Industry/Entity Type

Travel & Tourism / Aviation / Helicopter Tours / Experience‑based Activities

Requirements
Must have
• These elements are essential and must be included in the design: Brand & UX - Modern, upbeat, inviting design / SEO‑friendly structure and layout / Easy navigation and clear user flow / Light grey “SP” background logo watermark (as used on current site) / Clean, aviation‑inspired typography and layout
Nice to have
• Interactive route map showing flight paths / Subtle motion or parallax effects in hero sections / Animated icons or micro‑interactions / Social media integration (Instagram grid, TikTok clips) / Sticky mobile booking bar / Video header or short aerial footage loop / Subtle aviation‑themed graphic elements (rotor blur, sky gradients, etc.
Should not have
• No dark, heavy, or overly moody themes / No outdated fonts or overly playful typography / No cluttered layouts or excessive text blocks / No stocky, generic tourism imagery / No slow‑loading animations or heavy effects that hurt SEO

```html
<!DOCTYPE html>
<html lang="en">
<head>
<meta charset="utf-8">
<title>SkyPARLOR – Helicopter Tours in Florida</title>
<link rel="stylesheet" href="https://fonts.googleapis.com/css2?family=Rajdhani:wght@600;700&family=Mulish:wght@400;600;700&display=swap">
<style>
  :root {
    --blue: #1f4fd1;
    --blue-bright: #2563eb;
    --ink: #1d1d1f;
    --body: #4a4f57;
    --muted: #6b7078;
    --line: #8fb0ee;
    --section-grey: #e8ecf0;
    --white: #ffffff;
    --photo-warm-a: #c9a98a;
    --photo-warm-b: #5a4a3e;
  }
  * { box-sizing: border-box; margin: 0; padding: 0; }
  html, body { width: 1200px; height: 764px; overflow: hidden; background: var(--white); }
  body { position: relative; font-family: "Mulish", sans-serif; color: var(--ink); }

  /* About section */
  .about { position: absolute; left: 0; top: 0; width: 1200px; height: 470px; background: var(--white); }
  .about__accent { position: absolute; left: 118px; top: 20px; width: 122px; height: 100px; background: var(--blue); }
  .about__photo { position: absolute; left: 128px; top: 30px; width: 300px; height: 330px;
    background: linear-gradient(135deg, var(--photo-warm-a) 0%, #8c715c 55%, var(--photo-warm-b) 100%); }
  .about__content { position: absolute; left: 520px; top: 72px; width: 360px; }
  .eyebrow { display: flex; align-items: center; gap: 8px; font-family: "Rajdhani", sans-serif;
    font-weight: 700; font-size: 13px; color: var(--blue); }
  .eyebrow::before { content: ""; width: 20px; height: 2px; background: var(--blue); }
  .about__title { margin-top: 10px; font-family: "Rajdhani", sans-serif; font-weight: 700;
    font-size: 36px; line-height: 1.12; color: var(--ink); }
  .about__text { margin-top: 16px; font-size: 12px; line-height: 1.8; color: var(--body); }
  .button { display: inline-block; margin-top: 22px; padding: 9px 13px; background: var(--blue-bright);
    color: var(--white); font-family: "Rajdhani", sans-serif; font-weight: 700; font-size: 11px; text-decoration: none; }

  .stats { position: absolute; top: 372px; left: 0; width: 1200px; display: flex; justify-content: center; gap: 22px; }
  .stat { position: relative; width: 158px; height: 88px; border: 1px solid var(--line); border-bottom: none;
    text-align: center; padding-top: 14px; }
  .stat::before { content: ""; position: absolute; left: -5px; top: -5px; width: 10px; height: 10px;
    border-left: 2px solid var(--blue); border-top: 2px solid var(--blue); }
  .stat__value { font-family: "Rajdhani", sans-serif; font-weight: 700; font-size: 36px; line-height: 1; color: var(--blue); }
  .stat__label { margin-top: 10px; font-size: 10.5px; color: var(--muted); }

  /* Tours section */
  .tours { position: absolute; left: 0; top: 470px; width: 1200px; height: 294px; background: var(--section-grey); overflow: hidden; }
  .tours__head { text-align: center; padding-top: 14px; }
  .tours__head .eyebrow { justify-content: center; font-size: 10px; }
  .tours__head .eyebrow::after { content: ""; width: 14px; height: 2px; background: var(--blue); }
  .tours__head .eyebrow::before { width: 14px; }
  .tours__title { margin-top: 4px; font-family: "Rajdhani", sans-serif; font-weight: 600; font-size: 22px; line-height: 1.2; color: var(--ink); }
  .tour-track { position: absolute; top: 100px; left: 0; width: 1200px; height: 160px; }
  .tour-card { position: absolute; top: 0; height: 160px; color: var(--white); overflow: hidden; }
  .tour-card__media { position: absolute; inset: 0; }
  .tour-card__body { position: absolute; left: 16px; right: 16px; bottom: 14px; }
  .tour-card__title { font-family: "Rajdhani", sans-serif; font-weight: 700; font-size: 16px; }
  .tour-card__text { margin-top: 4px; font-size: 8.5px; line-height: 1.5; opacity: .9; }
  .tour-card__link { display: inline-block; margin-top: 6px; font-size: 8px; font-weight: 700; color: var(--white); text-decoration: underline; }
  .tour-card--tampa { left: 40px; width: 360px; }
  .tour-card--tampa .tour-card__media { background: linear-gradient(160deg, #7f95a6 0%, #3d4d58 100%); }
  .tour-card--sarasota { left: 406px; width: 388px; }
  .tour-card--sarasota .tour-card__media { background: linear-gradient(180deg, #c79a7a 0%, #5b6f86 45%, #1f3d4a 100%); }
  .tour-card--reveal { left: 800px; width: 360px; }
  .tour-card--reveal .tour-card__media { background: linear-gradient(160deg, #b9c2c9 0%, #5e707b 100%); }
  .pager { position: absolute; left: 0; top: 266px; width: 1200px; display: flex; flex-direction: column; align-items: center; gap: 4px; }
  .pager__count { font-size: 9px; font-weight: 700; color: var(--ink); }
  .pager__bar { width: 200px; height: 2px; background: var(--line); position: relative; }
  .pager__bar::before { content: ""; position: absolute; left: 0; top: 0; width: 67px; height: 2px; background: var(--blue); }
</style>
</head>
<body>
  <section class="about" aria-labelledby="about-title">
    <div class="about__accent"></div>
    <div class="about__photo" role="img" aria-label="Couple in helicopter headsets raising champagne glasses in the cabin"></div>
    <div class="about__content">
      <p class="eyebrow">Why SkyPARLOR</p>
      <h2 class="about__title" id="about-title">Premium Helicopter<br>Tours You Can Trust</h2>
      <p class="about__text">SkyPARLOR offers premium helicopter sightseeing experiences in Florida. We focus on safety, comfort, and unforgettable aerial views—whether you're a first-time flyer, a couple, or a family planning an exciting adventure.</p>
      <a class="button" href="#">Learn More About Us</a>
    </div>
    <div class="stats">
      <div class="stat"><div class="stat__value">15+</div><div class="stat__label">Years Experience</div></div>
      <div class="stat"><div class="stat__value">5-Star</div><div class="stat__label">Orbin Ratings</div></div>
      <div class="stat"><div class="stat__value">FAA</div><div class="stat__label">Certified Pilots</div></div>
      <div class="stat"><div class="stat__value">1,000</div><div class="stat__label">Thousands of Happy Flyers</div></div>
    </div>
  </section>

  <section class="tours" aria-labelledby="tours-title">
    <div class="tours__head">
      <p class="eyebrow">Our Tours</p>
      <h2 class="tours__title" id="tours-title">Choose Your<br>Perfect Helicopter Experience</h2>
    </div>
    <div class="tour-track">
      <article class="tour-card tour-card--tampa">
        <div class="tour-card__media" role="img" aria-label="Pilot in headset flying over the Tampa coast"></div>
        <div class="tour-card__body">
          <h3 class="tour-card__title">Tampa Helicopter Tours</h3>
          <p class="tour-card__text">Skyline, bay and iconic landmarks from the sky on custom flights.</p>
          <a class="tour-card__link" href="#">View Tampa Tours</a>
        </div>
      </article>
      <article class="tour-card tour-card--sarasota">
        <div class="tour-card__media" role="img" aria-label="Aerial view of Sarasota waterfront at sunset"></div>
        <div class="tour-card__body">
          <h3 class="tour-card__title">Sarasota Helicopter Tours</h3>
          <p class="tour-card__text">White sand beaches, turquoise waters, and stunning coastal views —<br>perfect for sightseeing, couples, and sunset lovers.</p>
          <a class="tour-card__link" href="#">View Sarasota Tours</a>
        </div>
      </article>
      <article class="tour-card tour-card--reveal">
        <div class="tour-card__media" role="img" aria-label="Helicopter over a marina during a gender reveal flight"></div>
        <div class="tour-card__body">
          <h3 class="tour-card__title">Gender Reveal Flights</h3>
          <p class="tour-card__text">Celebrate your special moment in the sky with a unique helicopter gender reveal.</p>
          <a class="tour-card__link" href="#">Explore Gender Reveal Flights</a>
        </div>
      </article>
    </div>
    <div class="pager">
      <span class="pager__count">1 / 3</span>
      <span class="pager__bar"></span>
    </div>
  </section>
</body>
</html>
```